Modern Business Card for Larkwell 2018

Our company assumes the best about people. We are creating an online community of entrepreneurs and business leaders who struggle with marketing their business online.

This business card should POP! We recently got a new logo and are launching a new website next month, so our business cards should make a statement that feels:
-Fresh
-Smart
-Trustworthy
-Fun

Target Market(s)

small business owners, entrepreneurs

Industry/Entity Type

Digital Marketing

Contact Information for Business Card

Dimensions: 3.5" x 2"

Font styles to use
Sans Serif

Colors
f37122
ffffff

Requirements
Must have
• We need a business card with a modern, bold design. We will use one side of the card as a lead-generation offer, so text on one side will need to fit up to 140 characters. The business card should stick to our core colors (orange, black, and white).
Nice to have
• We think a vertical "portrait" design could be interesting.
Should not have
• Should not look like a traditional business card. The round icon should stand out from a distance.

```html
<!DOCTYPE html>
<html lang="en">
<head>
<meta charset="utf-8">
<title>Larkwell Business Card</title>
<link rel="stylesheet" href="https://fonts.googleapis.com/css2?family=Open+Sans:wght@400;600;700;800&display=swap">
<style>
  :root {
    --orange: #f37122;
    --orange-deep: #e8611a;
    --black: #262626;
    --white: #ffffff;
    --field: #e6e6e6;
    --field-line: #555555;
    --canvas: #ece8e2;
  }
  * { box-sizing: border-box; margin: 0; padding: 0; }
  html, body {
    width: 1200px; height: 960px; overflow: hidden;
    background: var(--canvas);
    font-family: "Open Sans", sans-serif;
  }
  .sheet { position: relative; width: 1200px; height: 960px; }
  .card {
    position: absolute; left: 320px;
    width: 560px; height: 320px;
    border-radius: 4px;
    box-shadow: 0 6px 18px rgba(0,0,0,0.18);
    overflow: hidden;
  }

  /* Back: lead-generation offer */
  .card-offer { top: 120px; background: linear-gradient(180deg, var(--orange) 0%, var(--orange-deep) 100%); color: var(--white); }
  .offer-brand {
    position: absolute; left: 0; top: 0; width: 270px; height: 175px;
    display: flex; flex-direction: column; align-items: center; justify-content: center;
  }
  .offer-brand .mark { width: 26px; height: 26px; border-radius: 50%; background: var(--white); margin-bottom: 10px; }
  .offer-brand .wordmark { font-size: 38px; font-weight: 800; letter-spacing: 1px; line-height: 1; }
  .offer-brand .tagline { font-size: 10px; font-weight: 700; letter-spacing: 1.6px; margin-top: 6px; text-transform: uppercase; }
  .offer-divider { position: absolute; left: 276px; top: 26px; width: 1px; height: 140px; background: rgba(255,255,255,0.45); }
  .offer-copy { position: absolute; left: 296px; top: 26px; width: 250px; }
  .offer-headline { font-size: 17px; font-weight: 800; line-height: 1.05; text-transform: uppercase; }
  .offer-body { font-size: 12.5px; line-height: 1.35; margin-top: 8px; }
  .offer-url { font-size: 14px; font-weight: 700; margin-top: 8px; }
  .offer-field {
    position: absolute; left: 22px; right: 22px; top: 188px; height: 108px;
    background: var(--field); border-radius: 14px;
    box-shadow: inset 0 2px 4px rgba(0,0,0,0.12);
    padding: 30px 24px 0;
  }
  .offer-field .write-line { height: 1px; background: var(--field-line); margin-bottom: 32px; }

  /* Front: contact */
  .card-contact { top: 520px; background: var(--black); color: var(--white); text-align: center; }
  .contact-brand { margin-top: 56px; display: flex; flex-direction: column; align-items: center; }
  .contact-brand .mark { width: 110px; height: 110px; border-radius: 50%; background: var(--orange); }
  .contact-brand .wordmark { font-size: 14px; font-weight: 700; letter-spacing: 3px; color: var(--orange); margin-top: 10px; }
  .contact-name { font-size: 19px; font-weight: 700; color: var(--orange); text-transform: uppercase; margin-top: 14px; line-height: 1.1; }
  .contact-role { font-size: 15px; font-weight: 700; text-transform: uppercase; line-height: 1.2; }
  .contact-email { font-size: 15px; font-weight: 400; line-height: 1.3; }
</style>
</head>
<body>
<main class="sheet">
  <section class="card card-offer">
    <div class="offer-brand">
      <div class="mark"></div>
      <div class="wordmark">LARKWELL</div>
      <div class="tagline">Tell stories that inspire action</div>
    </div>
    <div class="offer-divider"></div>
    <div class="offer-copy">
      <p class="offer-headline">Reach more people.<br>Make more money.<br>Create more impact.</p>
      <p class="offer-body">Get your free Larkwell Starter Package and our marketing guide today at</p>
      <p class="offer-url">Larkwellnow.com/start</p>
    </div>
    <div class="offer-field">
      <div class="write-line"></div>
      <div class="write-line"></div>
    </div>
  </section>

  <section class="card card-contact">
    <div class="contact-brand">
      <div class="mark"></div>
      <div class="wordmark">LARKWELL</div>
    </div>
    <p class="contact-name">Dana Whitfield</p>
    <p class="contact-role">Story Marketing Coach</p>
    <p class="contact-email">dana@larkwellnow.com</p>
  </section>
</main>
</body>
</html>
```